Harborview Optical -Window Poster (Optometrist)

We are an optometry practice and we need a poster for a new store promotion for our window highlighting we now also sell 2 pairs of glasses as a package deal. The size will be 1300mm width x 1900mm height

The artwork will be displayed as a fabric banner in our shop window. We have 7 other banners with different services our business provides. The words needs to standout for passers by and the cars stopped at the traffic lights out front of our business. We already have signs with our logos phone number etc. so we won't need them included in the poster.

It would need to include the following information.

Two pair packages now available*

*Conditions apply

The artwork will be displayed as a fabric banner in our shop window. We have 7 other banners with different services our business provides. The words needs to standout for passers by and the cars stopped at the traffic lights out front of our business. We already have signs with our logos phone number etc. so we won't need them included in the poster. Thank you for your work it's amazing Added Saturday, February 18, 2017

The artwork will be displayed as a fabric banner in our shop window. We have 7 other banners with different services our business provides. The words needs to standout for passers by and the cars stopped at the traffic lights out front of our business. We already have signs with our logos phone number etc. so we won't need them included in the poster. Added Saturday, February 18, 2017

Target Market(s)

Cars driving past and stopped at traffic lights outside our store.

Industry/Entity Type

Optician

Requirements
Must have
• Poster must say:
• Two pair packages now available*
• *Conditions apply

```html
<!DOCTYPE html>
<html lang="en">
<head>
<meta charset="utf-8">
<title>Harborview Optical – Two Pair Packages Window Poster</title>
<link rel="stylesheet" href="https://fonts.googleapis.com/css2?family=Oswald:wght@700&family=Londrina+Solid:wght@900&display=swap">
<style>
  :root {
    --sky-top: #2a2f9e;
    --sky-mid: #3d5fc4;
    --sky-low: #5a86d8;
    --wood-light: #a39a7e;
    --wood-dark: #6f6650;
    --iris: #4fb8e6;
    --iris-deep: #1d7fc4;
    --band: #0c0a1e;
    --ink: #0d0b22;
    --sun: #f4ea1a;
    --orange: #e8922a;
    --white: #ffffff;
    --frame-red: #9a2a24;
    --bolt: #55585e;
  }
  html, body {
    margin: 0;
    padding: 0;
    width: 962px;
    height: 1200px;
    overflow: hidden;
    background: #ffffff;
  }
  .poster {
    position: relative;
    width: 962px;
    height: 1200px;
    overflow: hidden;
    background: linear-gradient(180deg, var(--sky-top) 0%, var(--sky-mid) 40%, var(--sky-low) 75%);
  }
  .wood-ledge {
    position: absolute;
    left: 0; top: 317px;
    width: 962px; height: 330px;
    background: linear-gradient(180deg, var(--wood-light), var(--wood-dark));
  }
  .wood-base {
    position: absolute;
    left: 0; top: 901px;
    width: 962px; height: 299px;
    background: linear-gradient(180deg, var(--wood-light) 0%, #8c8468 55%, var(--wood-dark) 100%);
  }
  .eye-art {
    position: absolute;
    left: 0; top: 0;
    width: 962px; height: 1200px;
  }
  .glasses-photo {
    position: absolute;
    left: 195px; top: 845px;
    width: 580px; height: 133px;
    border-radius: 0 0 120px 120px;
    background: linear-gradient(180deg, rgba(154,42,36,0.55), rgba(154,42,36,0.85));
  }
  .bolt {
    position: absolute;
    width: 92px; height: 92px;
    border-radius: 50%;
    background: radial-gradient(circle at 35% 35%, #b9bcc2, var(--bolt) 60%, #222 100%);
  }
  .bolt--left { left: 154px; top: 1121px; }
  .bolt--right { left: 757px; top: 1121px; }

  .headline-kicker {
    position: absolute;
    left: 0; top: 62px;
    width: 962px;
    text-align: center;
    font-family: "Oswald", sans-serif;
    font-weight: 700;
    font-size: 58px;
    letter-spacing: 2px;
    line-height: 1;
    color: var(--ink);
  }
  .headline-kicker .highlight { color: var(--sun); margin-left: 22px; }
  .headline-kicker .asterisk { color: var(--sun); font-size: 70px; vertical-align: 14px; }

  .band {
    position: absolute;
    left: 24px;
    width: 920px;
    background: var(--band);
    display: flex;
    align-items: center;
    justify-content: center;
    font-family: "Londrina Solid", sans-serif;
    font-weight: 900;
    line-height: 1;
    letter-spacing: 4px;
    paint-order: stroke fill;
  }
  .band--top { top: 230px; height: 191px; }
  .band--bottom { top: 600px; height: 194px; }
  .band__text--white {
    font-size: 178px;
    color: var(--white);
    -webkit-text-stroke: 10px var(--band);
    text-shadow: 0 0 0 var(--white), 4px 4px 0 var(--white), -4px -4px 0 var(--white), 4px -4px 0 var(--white), -4px 4px 0 var(--white);
  }
  .band__text--orange {
    font-size: 164px;
    color: var(--orange);
    -webkit-text-stroke: 10px var(--band);
    text-shadow: 4px 4px 0 var(--orange), -4px -4px 0 var(--orange), 4px -4px 0 var(--orange), -4px 4px 0 var(--orange);
  }

  .conditions {
    position: absolute;
    left: 121px; top: 1022px;
    width: 744px; height: 71px;
    border: 3px solid var(--ink);
    display: flex;
    align-items: center;
    justify-content: center;
    font-family: "Oswald", sans-serif;
    font-weight: 700;
    font-size: 46px;
    letter-spacing: 1px;
    color: var(--ink);
  }
</style>
</head>
<body>
  <main class="poster">
    <div class="wood-ledge" role="img" aria-label="Weathered timber ledge photograph"></div>
    <div class="wood-base" role="img" aria-label="Weathered timber board photograph"></div>

    <svg class="eye-art" viewBox="0 0 962 1200" role="img" aria-label="Stylised blue iris illustration">
      <defs>
        <radialGradient id="iris-fill" cx="50%" cy="50%" r="50%">
          <stop offset="0%" stop-color="#a9dcf3"/>
          <stop offset="60%" stop-color="#4fb8e6"/>
          <stop offset="100%" stop-color="#1d7fc4"/>
        </radialGradient>
      </defs>
      <ellipse cx="483" cy="517" rx="445" ry="374" fill="url(#iris-fill)"/>
    </svg>

    <div class="glasses-photo" role="img" aria-label="Photograph of red-framed glasses resting on the timber"></div>
    <div class="bolt bolt--left" role="img" aria-label="Metal bolt head"></div>
    <div class="bolt bolt--right" role="img" aria-label="Metal bolt head"></div>

    <p class="headline-kicker" style="margin:0">NOW<span class="highlight">AVAILABLE</span><span class="asterisk">*</span></p>

    <div class="band band--top"><span class="band__text--white">TWO PAIR</span></div>
    <div class="band band--bottom"><span class="band__text--orange">PACKAGES</span></div>

    <div class="conditions">*CONDITIONS APPLY</div>
  </main>
</body>
</html>
```